R7M Horizon Business Card Design

We need a business card created for our New Business "R7M Horizon"<br/><br/>The business card design is up to you however the following information must be on the business card:<br/><br/>Front of the business card -<br/>Email :darrenp@r7mhorizon.nz<br/>Mobile: +64 (0) 22 4870 619<br/>Website: www.r7mhorizon.nz<br/>Card Owner Name: Darren Paltrow<br/>Company Title: Business Development Manager<br/>Slogan: "Bold ideas, crafted well". <br/>Logo On the front attached to the design brief<br/><br/>On the back: <br/>Space on the back for 4 more versions of the logo across the bottom of the card indicating different subsidiary brands - R7M Coffee, R7M Arts, R7M ?? (The card will be used for all of these brands - We Will add the extra subsidiary logos to the design once the design is finished (We are a graphics design team). <br/><br/>Other than that we want a premium feeling logo that remains universally usable depending on the business entity that we are using the card for. The use of bright bold colours would be great but we still want the card to feel premium.
Target Market(s)
Gift Design and Manufacturing Companies
Contact Information for Business Card
Front of the business card -
Email :darrenp@r7mhorizon.nz
Mobile: +64 (0) 22 4870 619
Website: www.r7mhorizon.nz
Card Owner Name: Darren Paltrow
Company Title: Business Development Manager
Slogan: "Bold ideas, crafted well".
Logo On the front attached to the design brief

```html
<!DOCTYPE html>
<html lang="en">
<head>
<meta charset="utf-8">
<title>R7M Horizon Business Card</title>
<link rel="stylesheet" href="https://fonts.googleapis.com/css2?family=Montserrat:wght@400;500;600&display=swap">
<style>
  :root {
    --brand-blue: #26339a;
    --brand-blue-soft: #2f3ea8;
    --ink-dark: #2a2a2e;
    --paper: #f4f5f7;
    --rule-grey: #cfd0d6;
    --stage: #e6e7eb;
    --white: #ffffff;
  }
  * { margin: 0; padding: 0; box-sizing: border-box; }
  html, body {
    width: 1200px;
    height: 960px;
    overflow: hidden;
    background: var(--stage);
    font-family: "Montserrat", sans-serif;
  }
  .sheet {
    width: 1200px;
    height: 960px;
    display: flex;
    flex-direction: column;
    align-items: center;
    justify-content: center;
    gap: 60px;
  }
  .card {
    position: relative;
    width: 700px;
    height: 400px;
    overflow: hidden;
    box-shadow: 0 6px 18px rgba(0, 0, 0, 0.12);
  }
  /* Back */
  .card-back {
    background: var(--brand-blue);
    display: flex;
    align-items: center;
    justify-content: center;
  }
  .back-wordmark {
    display: flex;
    align-items: center;
    gap: 14px;
    color: var(--brand-blue-soft);
    font-weight: 600;
    font-size: 46px;
    letter-spacing: 1px;
  }
  .back-wordmark .mark-dot {
    width: 22px; height: 22px; border-radius: 50%;
    background: var(--brand-blue-soft);
  }
  /* Front */
  .card-front { background: var(--paper); }
  .card-front svg.front-art {
    position: absolute; inset: 0;
  }
  .front-wordmark {
    position: absolute;
    right: 70px;
    top: 92px;
    display: flex;
    align-items: center;
    gap: 12px;
    color: var(--brand-blue);
    font-weight: 600;
    font-size: 32px;
  }
  .front-wordmark .mark-dot {
    width: 16px; height: 16px; border-radius: 50%;
    background: var(--brand-blue);
  }
  .owner {
    position: absolute;
    left: 40px;
    top: 252px;
  }
  .owner-name {
    color: var(--brand-blue);
    font-size: 22px;
    font-weight: 500;
    line-height: 1.1;
  }
  .owner-title {
    color: var(--ink-dark);
    font-size: 14px;
    font-weight: 500;
    margin-top: 2px;
  }
  .contact-list {
    position: absolute;
    left: 40px;
    top: 306px;
    list-style: none;
  }
  .contact-list li {
    display: flex;
    align-items: center;
    gap: 10px;
    color: var(--ink-dark);
    font-size: 13.5px;
    height: 21px;
  }
  .contact-list svg { width: 13px; height: 13px; flex: none; }
  .slogan {
    position: absolute;
    right: 18px;
    top: 360px;
    color: var(--white);
    font-size: 15px;
    font-weight: 500;
    white-space: nowrap;
  }
</style>
</head>
<body>
<main class="sheet">
  <section class="card card-back" aria-label="Card back">
    <div class="back-wordmark"><span class="mark-dot"></span>R7M Horizon</div>
  </section>

  <section class="card card-front" aria-label="Card front">
    <svg class="front-art" viewBox="0 0 700 400" aria-hidden="true">
      <line x1="40" y1="238" x2="660" y2="226" stroke="var(--rule-grey)" stroke-width="1"/>
      <path d="M0 378 H436 C446 378 450 370 452 360 L455 348 C457 338 465 333 477 333 H700"
            fill="none" stroke="var(--ink-dark)" stroke-width="3"/>
      <path d="M0 386 H442 C452 386 457 378 459 368 L462 355 C464 346 470 341 481 341 H700 V400 H0 Z"
            fill="var(--brand-blue)"/>
    </svg>

    <div class="front-wordmark"><span class="mark-dot"></span>R7M Horizon</div>

    <div class="owner">
      <div class="owner-name">Darren Paltrow</div>
      <div class="owner-title">Business Development Manager</div>
    </div>

    <ul class="contact-list">
      <li>
        <svg viewBox="0 0 14 14"><rect x="3.5" y="1" width="7" height="12" rx="1.5" fill="none" stroke="var(--brand-blue)" stroke-width="1.6"/><circle cx="7" cy="10.6" r="0.9" fill="var(--brand-blue)"/></svg>
        +64 (0) 22 4870 619
      </li>
      <li>
        <svg viewBox="0 0 14 14"><rect x="1" y="3" width="12" height="8.5" fill="var(--brand-blue)"/><path d="M1 3 L7 8 L13 3" fill="none" stroke="#ffffff" stroke-width="1.2"/></svg>
        darrenp@r7mhorizon.nz
      </li>
      <li>
        <svg viewBox="0 0 14 14"><circle cx="7" cy="7" r="6" fill="var(--brand-blue)"/><path d="M1 7 H13 M7 1 C4 4 4 10 7 13 M7 1 C10 4 10 10 7 13" fill="none" stroke="#ffffff" stroke-width="0.9"/></svg>
        www.r7mhorizon.nz
      </li>
    </ul>

    <div class="slogan">Bold ideas, crafted well</div>
  </section>
</main>
</body>
</html>
```